Prosperity Pathway Basics PowerPoint

Please edit the following attached PowerPoint entitled workshop. Use the other attached PDF "TerraVesta Northern California Value Proposition" as a reference for the design and color I would like.

```html
<!DOCTYPE html>
<html lang="en">
<head>
<meta charset="utf-8">
<title>Prosperity Pathway Basics – Workshop Deck</title>
<link rel="stylesheet" href="https://fonts.googleapis.com/css2?family=Fira+Sans:wght@500;600;700;800&family=Poppins:wght@400;500;600;700&family=Noto+Serif:wght@400;700&display=swap">
<style>
:root{
  --stage:#9b9b9b;
  --navy:#0c2f78;
  --navy-deep:#08245f;
  --ink:#1f2a44;
  --blue:#1ea7ff;
  --sky:#a6d6f1;
  --sky-soft:#9fd0ee;
  --orange:#e8700f;
  --paper:#fbfcfe;
  --purple:#6b3e8f;
  --peach:#e9a35c;
  --teal:#3b88b6;
  --red:#c13449;
  --rowblue:#d9dff0;
  --rowpink:#e5aeae;
}
*{box-sizing:border-box;margin:0;padding:0}
html,body{width:1032px;height:1200px;overflow:hidden;background:var(--stage)}
body{font-family:"Poppins",sans-serif;color:var(--ink);position:relative}
.slide{position:absolute;width:477px;height:269px;overflow:hidden;background:var(--paper);box-shadow:0 1px 3px rgba(0,0,0,.25)}
.slide.dark{background:var(--navy);color:#fff}
.abs{position:absolute}
.title{position:absolute;left:16px;font-family:"Fira Sans",sans-serif;font-weight:700;color:var(--navy);font-size:14px;line-height:18px}
.rule{position:absolute;left:0;width:62px;height:1px;background:var(--blue)}
.rule::after{content:"";position:absolute;right:-2px;top:-2px;width:5px;height:5px;border-radius:50%;background:var(--blue)}
.brand{position:absolute;text-align:left;line-height:1}
.brand .name{font-family:"Poppins",sans-serif;font-weight:600;color:var(--navy);font-size:11.5px;display:flex;align-items:center;gap:3px}
.brand .name::before{content:"";width:5px;height:5px;border-radius:50%;background:currentColor}
.brand .sub{font-size:5.2px;color:var(--navy);margin-left:13px;margin-top:1px}
.dark .brand .name,.dark .brand .sub{color:#fff}
.footer{position:absolute;left:16px;top:242px;width:380px;height:15px;border-radius:8px;background:var(--sky);display:flex;align-items:center;padding-left:8px;font-size:3.8px;font-weight:600;color:var(--navy-deep)}
.footer span{display:flex;align-items:center;gap:1px;white-space:nowrap}
.footer span:nth-child(1){width:150px}
.footer span:nth-child(2){width:116px}
.footer svg{width:5px;height:5px;fill:var(--navy-deep)}
.footer .pg{position:absolute;right:3px;top:2.5px;width:10px;height:10px;border-radius:50%;background:#fff;font-size:4.2px;display:flex;align-items:center;justify-content:center;font-weight:700}
.photo{position:absolute}

/* slide 1 */
.s1 .lbl{font-weight:600;color:var(--blue);font-size:7.6px}
.s1 .pt{font-size:7.4px;color:#fff}
.s1 .tag{font-weight:600;color:var(--blue);font-size:8.4px;line-height:13.5px}

/* slide 2 */
.s2 .cap{position:absolute;font-size:9px;color:var(--ink)}
.s2 .frame{position:absolute;border-left:1px solid var(--navy);border-top:1px solid var(--navy)}

/* slide 3 */
.s3 .body{position:absolute;left:16px;font-size:7.8px;line-height:12.5px;color:var(--ink)}
.loss{position:absolute;display:flex;align-items:center;gap:5px;font-size:7.8px;font-weight:500;color:#111}
.loss i{width:27px;height:27px;border-radius:50%;background:radial-gradient(circle at 35% 30%,#2a6ccc,var(--navy-deep));display:flex;align-items:center;justify-content:center}
.loss svg{width:13px;height:13px;stroke:#fff;fill:none;stroke-width:1.6}

/* slide 4 */
.s4 h2{position:absolute;left:0;width:100%;top:81px;text-align:center;font-family:"Fira Sans",sans-serif;font-weight:800;font-size:18px;letter-spacing:.6px}
.s4 p{position:absolute;left:40px;width:397px;text-align:center;font-size:8.5px;line-height:14px}

/* slide 5 */
.box{position:absolute;display:flex;align-items:center;justify-content:center;text-align:center;border-radius:4px;font-size:7.5px;line-height:11px}
.box.orange{background:var(--orange);color:#fff}
.box.navy{background:var(--navy-deep);color:#fff}
.box.sky{background:var(--sky-soft);color:var(--navy);font-family:"Fira Sans",sans-serif;font-weight:700;font-size:8px;line-height:10px}
.box.term{background:#1896dd;color:#fff;font-weight:600;font-size:6.5px;border-radius:0}
.s5 .pts{position:absolute;left:16px;top:48px;font-size:8px;line-height:13px}

/* slide 6 */
.s6 .body{position:absolute;left:16px;top:75px;width:181px;font-size:6.1px;line-height:10.1px;text-align:justify;color:#333}
.s6 .body p+p{margin-top:4px}
.grid{position:absolute;left:221px;top:68px;width:238px;height:150px;background:#fff;font-family:"Noto Serif",serif}
.grid .gt{position:absolute;left:72px;top:2px;font-size:6.8px;color:var(--peach)}
.grid .ax{position:absolute;left:6px;top:110px;transform:rotate(-90deg);transform-origin:left top;font-size:6px;color:var(--peach);white-space:nowrap}
.grid .head{position:absolute;left:56px;top:14px;display:grid;grid-template-columns:repeat(5,36px);font-size:4.4px;font-weight:700;text-align:center;border-top:.5px solid #333;width:180px;padding-top:1px}
.grid .rows{position:absolute;left:13px;top:24px;display:grid;grid-template-columns:43px repeat(5,36px);grid-auto-rows:11.4px;font-size:4px;text-align:center}
.grid .rows b{font-weight:700;text-align:right;padding-right:6px;line-height:11.4px;border-top:.5px solid #333;color:#222}
.grid .rows span{color:#fff;line-height:11.4px;font-family:"Poppins",sans-serif;border:.3px solid rgba(255,255,255,.35)}
.c-p{background:var(--purple)}.c-o{background:var(--peach)}.c-t{background:var(--teal)}.c-r{background:var(--red)}

/* slide 7 */
.s7 .sub{position:absolute;left:16px;top:46px;font-size:7.5px}
.ladder{position:absolute;left:50px;top:71px;width:324px;border-collapse:collapse;font-size:7.3px}
.ladder th{background:#4678c3;color:#fff;text-align:left;font-family:"Fira Sans",sans-serif;font-weight:600;font-size:8.4px;height:17px;padding-left:4px;border-right:1px solid #fff}
.ladder td{background:var(--rowblue);border-bottom:1px solid #fff;padding:1px 4px;vertical-align:middle;color:#222}
.ladder td.n{width:15px;text-align:center;padding:0}
.ladder td.eff{width:59px;padding:0;background:var(--rowblue)}
.ladder tr.weak td:not(.eff){background:var(--rowpink)}
.ladder u{text-decoration:underline}
.ladder small{font-size:5px}
.ladder .ind{padding-left:12px;display:block}
.s7 .note{position:absolute;left:29px;top:199px;width:415px;font-size:4.6px;line-height:8.8px;color:#333}

/* slide 8 */
.s8 .big{position:absolute;left:0;width:100%;top:82px;display:flex;justify-content:center}
.s8 .big .brand{position:static}
.s8 .big .name{font-size:22px;gap:6px}
.s8 .big .name::before{width:9px;height:9px}
.s8 .big .sub{font-size:9.5px;margin-left:25px;margin-top:3px}
.s8 .ty{position:absolute;left:0;width:100%;top:129px;text-align:center;font-family:"Fira Sans",sans-serif;font-weight:700;font-size:15px}
.contact{position:absolute;top:163px;display:flex;gap:4px;font-size:3.9px;line-height:6.8px}
.contact i{width:17px;height:17px;border-radius:50%;background:#1e7fe0;display:flex;align-items:center;justify-content:center;flex:none}
.contact svg{width:8px;height:8px;fill:#fff}
.contact b{font-weight:700;display:block}
</style>
</head>
<body>

<svg width="0" height="0" style="position:absolute">
  <defs>
    <symbol id="pin" viewBox="0 0 10 10"><path d="M5 0a3.5 3.5 0 0 0-3.5 3.5C1.5 6 5 10 5 10s3.5-4 3.5-6.5A3.5 3.5 0 0 0 5 0zm0 5a1.5 1.5 0 1 1 0-3 1.5 1.5 0 0 1 0 3z"/></symbol>
    <symbol id="globe" viewBox="0 0 10 10"><path d="M5 0a5 5 0 1 0 0 10A5 5 0 0 0 5 0zm3.9 4.5H7a8 8 0 0 0-.7-3.2 4 4 0 0 1 2.6 3.2zM5 1c.5.6.9 2 1 3.5H4C4.1 3 4.5 1.6 5 1zM3.7 1.3A8 8 0 0 0 3 4.5H1.1a4 4 0 0 1 2.6-3.2zM1.1 5.5H3a8 8 0 0 0 .7 3.2 4 4 0 0 1-2.6-3.2zM5 9c-.5-.6-.9-2-1-3.5h2C5.9 7 5.5 8.4 5 9zm1.3-.3A8 8 0 0 0 7 5.5h1.9a4 4 0 0 1-2.6 3.2z"/></symbol>
    <symbol id="phone" viewBox="0 0 10 10"><path d="M2 0l2 2.3-1 1.3a6 6 0 0 0 3.4 3.4l1.3-1L10 8l-1 1.6C8.5 10 7.5 10 6 9.3A9.5 9.5 0 0 1 .7 4C0 2.5 0 1.5.4 1z"/></symbol>
  </defs>
</svg>

<!-- Slide 01 -->
<section class="slide dark s1" style="left:29px;top:28px">
  <div class="photo" role="img" aria-label="Photo of a hand passing a burlap money bag marked with a dollar sign over a sunny green field" style="left:246px;top:-32px;width:262px;height:262px;border-radius:50%;background:radial-gradient(circle at 60% 25%,#f4d98a 0,#c9a45b 22%,#8fae55 48%,#4f8a3a 70%,#2f6a2e 100%)"></div>
  <div class="brand" style="left:16px;top:27px"><div class="name" style="color:#fff;font-size:14px">TerraVesta</div><div class="sub" style="font-size:7px;margin-left:18px">Northern California</div></div>
  <div class="title" style="top:64px;color:#fff;font-size:20px;line-height:24px;font-weight:800">YOUR MONEY</div>
  <div class="rule" style="top:95px;background:var(--blue)"></div>
  <div class="abs lbl" style="left:16px;top:107px">Objective :</div>
  <div class="abs pt" style="left:16px;top:120px">• Build as big as possible</div>
  <div class="abs lbl" style="left:16px;top:138px">How:</div>
  <div class="abs pt" style="left:16px;top:151px;line-height:12.5px">• Higher rates of return?<br>• More risk?<br>• "Better" products?</div>
  <div class="abs tag" style="left:16px;top:197px">Having an efficient overall strategy is the<br>key; it all starts here!</div>
  <div class="footer"><span><svg><use href="#pin"/></svg>| 4820 Orchard Ridge Way Suite #210, Pleasanton, CA 94566</span><span><svg><use href="#globe"/></svg>| www.northerncalifornia.terravesta.com</span><span><svg><use href="#phone"/></svg>| 925-555-0148</span><b class="pg">01</b></div>
</section>

<!-- Slide 02 -->
<section class="slide s2" style="left:526px;top:28px">
  <div class="title" style="top:12px;font-weight:800">YOUR MONEY</div>
  <div class="rule" style="top:36px"></div>
  <div class="brand" style="left:379px;top:14px"><div class="name">TerraVesta</div><div class="sub">Northern California</div></div>
  <div class="cap" style="left:88px;top:55px">Equipment and Tools</div>
  <div class="cap" style="left:289px;top:55px">Skill and Technique</div>
  <div class="frame" style="left:85px;top:77px;width:100px;height:95px"></div>
  <div class="photo" role="img" aria-label="Photo of climbing gear: ropes, carabiners and shoes piled on rock" style="left:88px;top:81px;width:122px;height:117px;background:linear-gradient(135deg,#5d4a38,#8a6a4a 40%,#c2553c 60%,#3f5f86 80%,#6a5440)"></div>
  <div class="frame" style="left:287px;top:77px;width:100px;height:95px"></div>
  <div class="photo" role="img" aria-label="Photo of an ice climber in red ascending a frozen wall" style="left:290px;top:81px;width:122px;height:117px;background:linear-gradient(160deg,#dfe6ef,#b7c4d6 45%,#8ea2bf 70%,#e9edf3)"></div>
  <div class="abs" style="left:242px;top:135px;font-weight:700;color:var(--navy);font-size:9.5px">VS</div>
  <div class="cap" style="left:86px;top:208px">Products</div>
  <div class="cap" style="left:294px;top:208px">Strategy</div>
  <div class="footer"><span><svg><use href="#pin"/></svg>| 4820 Orchard Ridge Way Suite #210, Pleasanton, CA 94566</span><span><svg><use href="#globe"/></svg>| www.northerncalifornia.terravesta.com</span><span><svg><use href="#phone"/></svg>| 925-555-0148</span><b class="pg">02</b></div>
</section>

<!-- Slide 03 -->
<section class="slide s3" style="left:29px;top:320px">
  <div class="title" style="top:11px">Why is Your Strategy so Important?</div>
  <div class="rule" style="top:38px"></div>
  <div class="brand" style="left:379px;top:13px"><div class="name">TerraVesta</div><div class="sub">Northern California</div></div>
  <div class="body" style="top:47px;width:340px">We all only have a finite amount of money…we have to be efficient with it in the short time we have.</div>
  <div class="body" style="top:75px">Inefficiencies cause major losses to occur</div>
  <div class="body" style="top:88px;color:var(--navy);font-weight:500">These losses can be reflected in:</div>

  <div class="loss" style="left:16px;top:114px"><i><svg viewBox="0 0 14 14"><circle cx="7" cy="7" r="2.5"/><path d="M7 1v2M7 11v2M1 7h2M11 7h2M3 3l1.4 1.4M9.6 9.6 11 11M3 11l1.4-1.4M9.6 4.4 11 3"/></svg></i>lower current lifestyle</div>
  <div class="loss" style="left:153px;top:114px"><i><svg viewBox="0 0 14 14"><rect x="2" y="4" width="10" height="7" rx="1"/><circle cx="7" cy="7.5" r="1.6"/></svg></i>lower retirement income</div>
  <div class="loss" style="left:302px;top:114px"><i><svg viewBox="0 0 14 14"><circle cx="7" cy="4" r="2"/><path d="M3 12c0-2.5 1.8-4 4-4s4 1.5 4 4"/><circle cx="2.5" cy="6" r="1.3"/><circle cx="11.5" cy="6" r="1.3"/></svg></i>inadequate protection</div>
  <div class="loss" style="left:16px;top:152px"><i><svg viewBox="0 0 14 14"><path d="M2 12V9M5 12V7M8 12V5M11 12V3"/></svg></i>loss of financial control</div>
  <div class="loss" style="left:153px;top:152px"><i><svg viewBox="0 0 14 14"><path d="M7 1.5 12 3.5v3.5c0 3-2.2 5-5 5.5-2.8-.5-5-2.5-5-5.5V3.5z"/></svg></i>financial vulnerability</div>
  <div class="loss" style="left:302px;top:152px"><i><svg viewBox="0 0 14 14"><path d="M3.5 1.5h5l2.5 2.5v8.5h-7.5z"/><path d="M5.5 6h3M5.5 8.5h3"/></svg></i>higher taxes and fees</div>
  <div class="loss" style="left:16px;top:194px"><i><svg viewBox="0 0 14 14"><path d="M2 11h4l4-2.5M5 8V5M8 7V3M11 6V2"/></svg></i>less benefits</div>
  <div class="footer"><span><svg><use href="#pin"/></svg>| 4820 Orchard Ridge Way Suite #210, Pleasanton, CA 94566</span><span><svg><use href="#globe"/></svg>| www.northerncalifornia.terravesta.com</span><span><svg><use href="#phone"/></svg>| 925-555-0148</span><b class="pg">03</b></div>
</section>

<!-- Slide 04 -->
<section class="slide dark s4" style="left:526px;top:320px">
  <div class="photo" role="img" aria-label="Photo of a seedling growing from stacked coins beside rising bar shapes, tinted deep blue" style="left:0;top:0;width:477px;height:269px;background:radial-gradient(ellipse at 20% 75%,#2c4f8a 0,transparent 55%),linear-gradient(180deg,#123a80,#0c2f78 60%,#0a2a6b)"></div>
  <h2>HOW SIGNIFICANT IS EFFICIENCY?</h2>
  <p style="top:119px">An individual might be able to create $75,000/year (1 unit) of retirement income based on current savings with an inefficient process</p>
  <p style="top:154px">The same individual could create $125,000/year of retirement income with an efficient process using the same amount of savings.</p>
  <div class="footer" style="width:360px"><span><svg><use href="#pin"/></svg>| 4820 Orchard Ridge Way Suite #210, Pleasanton, CA 94566</span><span><svg><use href="#globe"/></svg>| www.northerncalifornia.terravesta.com</span><span><svg><use href="#phone"/></svg>| 925-555-0148</span><b class="pg">04</b></div>
  <div class="brand" style="left:399px;top:243px"><div class="name" style="font-size:9px">TerraVesta</div><div class="sub" style="font-size:4.2px;margin-left:10px">Northern California</div></div>
</section>

<!-- Slide 05 -->
<section class="slide s5" style="left:29px;top:612px">
  <div class="title" style="top:11px">Pathway Blueprint™</div>
  <div class="rule" style="top:37px"></div>
  <div class="brand" style="left:379px;top:13px"><div class="name">TerraVesta</div><div class="sub">Northern California</div></div>
  <div class="pts">• Protection (Your Safety Shield)<br>• Wealth Building</div>
  <svg class="abs" style="left:0;top:0" width="477" height="269" viewBox="0 0 477 269">
    <g fill="none" stroke="#9aa7b8" stroke-width=".6">
      <path d="M312 75.5h7M319 57v42M319 57h13M319 78.5h13M319 99h13"/>
      <path d="M306 191h8M314 168v41M314 168h13M314 188.5h13M314 209h13"/>
    </g>
    <line x1="206" y1="79" x2="172" y2="108" stroke="var(--orange)" stroke-width="1.6"/>
    <path d="M168 111.5l3.2-8 4.8 5.4z" fill="var(--orange)"/>
    <line x1="167" y1="156" x2="201" y2="186" stroke="#1896dd" stroke-width="1.6"/>
    <path d="M205 189.5l-8-3 5.3-5z" fill="#1896dd"/>
  </svg>
  <div class="box orange" style="left:217px;top:55px;width:95px;height:41px">Protection<br>(Your Safety Shield)</div>
  <div class="box orange" style="left:332px;top:50px;width:74px;height:15px">Protection</div>
  <div class="box orange" style="left:332px;top:71px;width:74px;height:15px">Protection</div>
  <div class="box orange" style="left:332px;top:91px;width:74px;height:16px">Protection</div>
  <div class="box sky" style="left:71px;top:115px;width:94px;height:39px">Pathway<br>Blueprint™</div>
  <div class="box navy" style="left:212px;top:171px;width:94px;height:40px">Protection<br>(Your Safety Shield)</div>
  <div class="box navy" style="left:327px;top:160px;width:75px;height:16px">Protection</div>
  <div class="box navy" style="left:327px;top:181px;width:75px;height:15px">Protection</div>
  <div class="box navy" style="left:327px;top:201px;width:75px;height:16px">Protection</div>
  <div class="box term" style="left:407px;top:160px;width:50px;height:16px">Short Term</div>
  <div class="box term" style="left:407px;top:181px;width:50px;height:36px">Long Term</div>
  <div class="footer"><span><svg><use href="#pin"/></svg>| 4820 Orchard Ridge Way Suite #210, Pleasanton, CA 94566</span><span><svg><use href="#globe"/></svg>| www.northerncalifornia.terravesta.com</span><span><svg><use href="#phone"/></svg>| 925-555-0148</span><b class="pg">05</b></div>
</section>

<!-- Slide 06 -->
<section class="slide s6" style="left:526px;top:612px">
  <div class="title" style="top:11px">An Attempted Solution for Pulling Income<br>from Your Investments in Retirement</div>
  <div class="rule" style="top:54px"></div>
  <div class="brand" style="left:379px;top:13px"><div class="name">TerraVesta</div><div class="sub">Northern California</div></div>
  <div class="body">
    <p>The chart below shows the likelihood a portfolio will last 30 years based on different portfolio allocations and various withdrawal rates. As the key shows, however, there are trade-offs between security and flexibility.</p>
    <p>A lower withdrawal rate could result in a higher likelihood of the portfolio lasting, but with an unnecessary sacrifice to lifestyle or undue investment risk.</p>
    <p>On the flip side, if a retiree's withdrawal rate is too high, they run the risk of outliving their savings.This chart can help you think about what withdrawal rate you could be comfortable using in the systematic withdrawal option on the previous page.</p>
  </div>
  <div class="grid">
    <div class="gt">30-Year Period Stock/Bond Allocation (%)</div>
    <div class="ax">Withdrawal rate (%)</div>
    <div class="head"><span>20/80</span><span>40/60</span><span>60/40</span><span>80/20</span><span>100/0</span></div>
    <div class="rows">
      <b>1</b><span class="c-p">90%-100%</span><span class="c-p">90%-100%</span><span class="c-p">90%-100%</span><span class="c-p">90%-100%</span><span class="c-p">90%-100%</span>
      <b>2</b><span class="c-p">90%-100%</span><span class="c-p">90%-100%</span><span class="c-p">90%-100%</span><span class="c-p">90%-100%</span><span class="c-p">90%-100%</span>
      <b>3</b><span class="c-p">90%-100%</span><span class="c-p">90%-100%</span><span class="c-o">80%-90%</span><span class="c-o">80%-90%</span><span class="c-o">80%-90%</span>
      <b>4</b><span class="c-t">40%-50%</span><span class="c-t">50%-60%</span><span class="c-t">60%-70%</span><span class="c-t">60%-70%</span><span class="c-t">60%-70%</span>
      <b>5</b><span class="c-r">0%-10%</span><span class="c-t">20%-30%</span><span class="c-t">30%-40%</span><span class="c-t">40%-50%</span><span class="c-t">50%-60%</span>
      <b>6</b><span class="c-r">0%-10%</span><span class="c-r">0%-10%</span><span class="c-t">10%-20%</span><span class="c-t">30%-40%</span><span class="c-t">30%-40%</span>
      <b>7</b><span class="c-r">0%-10%</span><span class="c-r">0%-10%</span><span class="c-r">0%-10%</span><span class="c-t">10%-20%</span><span class="c-t">20%-30%</span>
      <b>8</b><span class="c-r">0%-10%</span><span class="c-r">0%-10%</span><span class="c-r">0%-10%</span><span class="c-r">0%-10%</span><span class="c-r">0%-10%</span>
      <b>9</b><span class="c-r">0%-10%</span><span class="c-r">0%-10%</span><span class="c-r">0%-10%</span><span class="c-r">0%-10%</span><span class="c-r">0%-10%</span>
      <b>10</b><span class="c-r">0%-10%</span><span class="c-r">0%-10%</span><span class="c-r">0%-10%</span><span class="c-r">0%-10%</span><span class="c-r">0%-10%</span>
    </div>
  </div>
  <div class="footer"><span><svg><use href="#pin"/></svg>| 4820 Orchard Ridge Way Suite #210, Pleasanton, CA 94566</span><span><svg><use href="#globe"/></svg>| www.northerncalifornia.terravesta.com</span><span><svg><use href="#phone"/></svg>| 925-555-0148</span><b class="pg">06</b></div>
</section>

<!-- Slide 07 -->
<section class="slide s7" style="left:29px;top:904px">
  <div class="title" style="top:11px">Retirement Income Strategy Hierarchy</div>
  <div class="rule" style="top:35px"></div>
  <div class="brand" style="left:379px;top:13px"><div class="name">TerraVesta</div><div class="sub">Northern California</div></div>
  <div class="sub">(Highest to Lowest Efficiency)</div>
  <table class="ladder">
    <tr><th style="width:15px;padding:0"></th><th>Retirement Income Strategies</th><th style="border-right:0">Efficiency</th></tr>
    <tr style="height:37px"><td class="n">1</td><td><u>Twin Growth Engines® Approach:</u><span class="ind">- Covered Assets Option <small>(Guaranteed*)</small></span><span class="ind">- Volatility Buffer Option <small>(Non-Guaranteed)</small></span></td>
      <td class="eff" rowspan="4" style="position:relative">
        <svg width="59" height="90" viewBox="0 0 59 90" style="display:block">
          <defs><linearGradient id="upfade" x1="0" y1="0" x2="0" y2="1"><stop offset="0" stop-color="#2f6fc6"/><stop offset="1" stop-color="#a9c6ee"/></linearGradient></defs>
          <path d="M29.5 4 44 21h-8v65H23V21h-8z" fill="url(#upfade)" stroke="#2f6fc6" stroke-width=".6"/>
        </svg>
      </td></tr>
    <tr style="height:16px"><td class="n">2</td><td>Joint Single Premium Immediate Annuity <small>(Guaranteed*)</small></td></tr>
    <tr style="height:16px"><td class="n">3</td><td>Growth Annuity with Income Rider <small>(Guaranteed*)</small></td></tr>
    <tr class="weak" style="height:24px"><td class="n">4</td><td><u>Single Growth Engine™ Approach:</u><br>Investments Only using Withdrawal Rate Simulations <small>(Non-Guaranteed)</small></td></tr>
  </table>
  <div class="note">This chart is meant to show the concept of efficiency for different retirement income strategies. Efficiencies will vary overtime and past performance is not indicative of future results. *These strategies should notbe considered to provide any income, money, or benefits that are at this time guaranteed. Guarantees occur at the time a product is purchased that provides those guarantees, and at that time the guarantees are based on the claims-paying ability of the issuing company.</div>
  <div class="footer"><span><svg><use href="#pin"/></svg>| 4820 Orchard Ridge Way Suite #210, Pleasanton, CA 94566</span><span><svg><use href="#globe"/></svg>| www.northerncalifornia.terravesta.com</span><span><svg><use href="#phone"/></svg>| 925-555-0148</span><b class="pg">06</b></div>
</section>

<!-- Slide 08 -->
<section class="slide dark s8" style="left:526px;top:904px">
  <div class="big"><div class="brand"><div class="name">TerraVesta</div><div class="sub">Northern California</div></div></div>
  <div class="ty">Thank You</div>
  <div class="contact" style="left:89px"><i><svg><use href="#pin"/></svg></i><div><b>LOCATION :</b>4820 Orchard Ridge Way Suite #210,<br>Pleasanton, CA 94566</div></div>
  <div class="contact" style="left:202px"><i><svg><use href="#globe"/></svg></i><div><b>WEBSITE :</b>www.northerncalifornia.terravesta.com</div></div>
  <div class="contact" style="left:327px"><i><svg><use href="#phone"/></svg></i><div><b>PHONE NUMBER:</b>925-555-0148</div></div>
</section>

</body>
</html>
```